Coastline Premier Retreats Business Card Design

Design a business card for Coastline Premier Retreats. Look at the website for colors and reference. Card should have logo, name, title, office number, mobile number, email, URL and a tagline like, "Luxury Hotel & Resort Email Marketing" (This might change).

https://www.coastlinepremierretreats.example

The rest I will leave up to your imagination.

Contact Information for Business Card

Logo, name, title, office number, mobile number, email, URL and a tagline like, "Luxury Hotel & Resort Email Marketing" (This might change).

```html
<!DOCTYPE html>
<html lang="en">
<head>
<meta charset="utf-8">
<title>Coastline Premier Retreats – Business Card</title>
<link rel="stylesheet" href="https://fonts.googleapis.com/css2?family=Open+Sans:wght@400;600;700&display=swap">
<style>
  :root {
    --bg: #242424;
    --card: #1e1e21;
    --orange: #f37321;
    --white: #ffffff;
    --muted: #d9d9d9;
    --rule: #8a8a8a;
  }
  * { box-sizing: border-box; margin: 0; padding: 0; }
  html, body { width: 1200px; height: 780px; overflow: hidden; background: var(--bg); }
  body {
    font-family: "Open Sans", Arial, sans-serif;
    display: flex; align-items: center; justify-content: center; gap: 56px;
  }
  .card {
    position: relative;
    width: 540px; height: 309px;
    background: var(--card);
    box-shadow: 0 18px 40px rgba(0,0,0,.45);
    overflow: hidden;
  }
  .brand {
    display: flex; align-items: center; gap: 10px;
    color: var(--white); font-weight: 700; letter-spacing: .02em;
  }
  .brand-square { width: 14px; height: 14px; background: var(--orange); flex: none; }

  /* front */
  .card-front .brand { position: absolute; top: 44px; right: 40px; font-size: 22px; }
  .identity { position: absolute; top: 112px; left: 40px; text-align: right; width: 200px; }
  .person-name { font-size: 25px; font-weight: 700; color: var(--white); line-height: 1.1; }
  .person-name .first { color: var(--orange); }
  .person-title { font-size: 13px; color: var(--muted); margin-top: 4px; }
  .divider {
    position: absolute; top: 112px; left: 262px;
    width: 1px; height: 92px; background: var(--rule);
  }
  .contact-list {
    position: absolute; top: 112px; left: 282px;
    list-style: none; font-size: 12.5px; color: var(--white); line-height: 1;
  }
  .contact-list li { display: flex; align-items: center; gap: 8px; margin-bottom: 9px; }
  .contact-list svg { width: 13px; height: 13px; flex: none; fill: none; stroke: var(--orange); stroke-width: 2; }
  .tagline-band {
    position: absolute; left: 0; right: 0; bottom: 18px; height: 30px;
    background: var(--orange); color: var(--white);
    font-size: 13.5px; display: flex; align-items: center; padding-left: 40px;
  }

  /* back */
  .card-back { display: flex; align-items: center; justify-content: center; }
  .card-back .brand { font-size: 28px; }
  .card-back .brand-square { width: 18px; height: 18px; }
</style>
</head>
<body>
  <section class="card card-front">
    <div class="brand"><span class="brand-square"></span>Coastline Premier Retreats</div>

    <div class="identity">
      <p class="person-name"><span class="first">Mara</span> Lindqvist</p>
      <p class="person-title">Co-Founder</p>
    </div>

    <div class="divider"></div>

    <ul class="contact-list">
      <li>
        <svg viewBox="0 0 24 24"><path d="M5 3h4l2 5-3 2a11 11 0 0 0 6 6l2-3 5 2v4a2 2 0 0 1-2 2A17 17 0 0 1 3 5a2 2 0 0 1 2-2z"/></svg>
        (555) 014-2758
      </li>
      <li>
        <svg viewBox="0 0 24 24"><rect x="6" y="2" width="12" height="20" rx="2"/><line x1="11" y1="18" x2="13" y2="18"/></svg>
        (555) 017-7777
      </li>
      <li>
        <svg viewBox="0 0 24 24"><circle cx="12" cy="12" r="9"/><path d="M3 12h18M12 3a14 14 0 0 1 0 18M12 3a14 14 0 0 0 0 18"/></svg>
        www.coastlinepremierretreats.example
      </li>
      <li>
        <svg viewBox="0 0 24 24"><rect x="3" y="5" width="18" height="14" rx="1"/><path d="M3 6l9 7 9-7"/></svg>
        info@coastlinepremierretreats.example
      </li>
    </ul>

    <div class="tagline-band">Luxury Hotel &amp; Resort Email Marketing</div>
  </section>

  <section class="card card-back">
    <div class="brand"><span class="brand-square"></span>Coastline Premier Retreats</div>
  </section>
</body>
</html>
```